Every Shelf Set Neatly or ESN Organized needs a business card design. ESN Organized is a professi

We need a business card design that is clean, sharp and conveys a sense of organization. I already have a logo.

Target Market(s)

Families (specifically mothers), small business owners, parents, seniors

Industry/Entity Type

Business

Contact Information for Business Card

My website is www.esnorganized-example.com and my Facebook page is http://www.sociallink-example.com/everyshelfsetneatly. The phone number is 418-552-7094 and I want to be listed as Lorna M. Pelham, Owner

Requirements
Must have
• My logo.

```html
<!DOCTYPE html>
<html lang="en">
<head>
<meta charset="utf-8">
<title>ESN Organized — Business Card</title>
<link href="https://fonts.googleapis.com/css2?family=Source+Sans+3:wght@400;600&display=swap" rel="stylesheet">
<style>
  :root {
    --backdrop: #ecebe9;
    --card-blue: #0a7cdb;
    --card-black: #000000;
    --text-white: #ffffff;
    --brand-blue: #1a86e8;
  }
  html, body {
    margin: 0;
    padding: 0;
    width: 1200px;
    height: 900px;
    overflow: hidden;
    background: var(--backdrop);
    font-family: "Source Sans 3", "Myriad Pro", Arial, sans-serif;
  }
  .canvas {
    position: relative;
    width: 1200px;
    height: 900px;
  }
  .card {
    position: absolute;
    box-shadow: 0 6px 18px rgba(0,0,0,0.18);
    overflow: hidden;
  }
  /* Front of card */
  .card-front {
    left: 238px;
    top: 62px;
    width: 555px;
    height: 343px;
    background: var(--card-blue);
    color: var(--text-white);
  }
  .side-panel {
    position: absolute;
    right: 0;
    top: 0;
    width: 172px;
    height: 100%;
    background: var(--card-black);
  }
  .owner-name {
    position: absolute;
    left: 38px;
    top: 60px;
    margin: 0;
    font-size: 19px;
    font-weight: 600;
    line-height: 1;
  }
  .owner-title {
    position: absolute;
    left: 38px;
    top: 84px;
    margin: 0;
    font-size: 15px;
    font-weight: 400;
  }
  .contact-list {
    position: absolute;
    left: 32px;
    top: 191px;
    margin: 0;
    padding: 0;
    list-style: none;
    font-size: 15px;
    line-height: 20px;
  }
  .contact-list li {
    display: flex;
    align-items: center;
    gap: 8px;
  }
  .contact-icon {
    width: 12px;
    height: 12px;
    fill: var(--text-white);
    flex: none;
  }
  .social-link {
    position: absolute;
    left: 32px;
    top: 277px;
    margin: 0;
    font-size: 15px;
  }
  /* Back of card */
  .card-back {
    left: 457px;
    top: 518px;
    width: 560px;
    height: 344px;
    background: var(--card-black);
  }
  .brand-name {
    position: absolute;
    left: 0;
    right: 0;
    top: 152px;
    margin: 0;
    text-align: center;
    font-size: 36px;
    font-weight: 400;
    letter-spacing: 3px;
    color: var(--brand-blue);
    line-height: 1;
  }
</style>
</head>
<body>
<main class="canvas">
  <section class="card card-front" aria-label="Card front">
    <div class="side-panel"></div>
    <h1 class="owner-name">Lorna M. Pelham</h1>
    <p class="owner-title">Owner</p>
    <ul class="contact-list">
      <li>
        <svg class="contact-icon" viewBox="0 0 12 12" aria-hidden="true"><path d="M2.4 0.6l1.8 2.4-1 1.2c0.7 1.5 1.9 2.8 3.5 3.6l1.2-1 2.4 1.8-0.9 2.2C5.4 10.6 1.3 6.5 0.2 1.6z"/></svg>
        418-552-7094
      </li>
      <li>
        <svg class="contact-icon" viewBox="0 0 12 12" aria-hidden="true"><path d="M1 3h10v6.5H1z M1.3 3.3L6 6.6l4.7-3.3" stroke="#0a7cdb" stroke-width="0.9"/></svg>
        info@esnorganized-example.com
      </li>
      <li>
        <svg class="contact-icon" viewBox="0 0 12 12" aria-hidden="true"><circle cx="6" cy="6" r="5.2"/><path d="M1 6h10M6 1c-2.2 2.8-2.2 7.2 0 10M6 1c2.2 2.8 2.2 7.2 0 10" stroke="#0a7cdb" stroke-width="0.8" fill="none"/></svg>
        www.esnorganized-example.com
      </li>
    </ul>
    <p class="social-link">www.sociallink-example.com/everyshelfsetneatly</p>
  </section>

  <section class="card card-back" aria-label="Card back">
    <p class="brand-name">ESN Organized</p>
  </section>
</main>
</body>
</html>
```